Healthcare and Professional IT Services Company need a redesigned business card

We are a IT Services company that targets small medical practices and professional business such as Attorneys, Accounts, Architects etc. We want to communicate a professional yet friendly image using recent logo redesign here on ArtHarbor. Like to see the colors blue and orange in the design. Must use the Tall Pine Computing as displayed in the new logo - then also want to incorporate the fish logo as well.

Target Market(s)

Small medical and professional services

Industry/Entity Type

It Company

Contact Information for Business Card

The usual stuff, place for name address phone website. Also maybe our tagline which is "Rooted in technology"

Requirements
Must have
• My new logo and the fish somewhere on the card

```html
<!DOCTYPE html>
<html lang="en">
<head>
<meta charset="utf-8">
<title>Tall Pine Computing – Business Card</title>
<link rel="stylesheet" href="https://fonts.googleapis.com/css2?family=Source+Sans+3:wght@400;600;700&display=swap">
<style>
  :root {
    --backdrop: #3b3b3b;
    --paper: #f7f7f7;
    --brand-blue: #1a8fd6;
    --deep-blue: #116cb4;
    --accent-orange: #f2961e;
    --ink: #444;
    --rule: #d2d2d2;
    --white: #ffffff;
  }
  * { margin: 0; padding: 0; box-sizing: border-box; }
  html, body {
    width: 1200px; height: 750px; overflow: hidden;
    background: var(--backdrop);
    font-family: "Source Sans 3", sans-serif;
  }
  .canvas { position: relative; width: 1200px; height: 750px; }
  .card {
    position: absolute; top: 228px;
    width: 462px; height: 262px; overflow: hidden;
  }
  .card--front { left: 124px; background: var(--paper); }
  .card--back { left: 618px; background: var(--deep-blue); }

  .brand {
    position: absolute; display: flex; align-items: center; gap: 8px;
    font-weight: 600; font-size: 17px; white-space: nowrap;
  }
  .brand__dot { width: 16px; height: 16px; border-radius: 50%; flex: none; }
  .card--front .brand { left: 40px; top: 118px; color: var(--brand-blue); }
  .card--front .brand__dot { background: var(--brand-blue); }
  .card--back .brand { left: 50%; top: 116px; transform: translateX(-50%); color: var(--white); font-size: 19px; }
  .card--back .brand__dot { background: var(--white); }

  .divider {
    position: absolute; left: 238px; top: 56px;
    width: 1px; height: 150px; background: var(--rule);
  }
  .contact { position: absolute; left: 263px; top: 60px; color: var(--ink); }
  .contact__name { font-size: 18px; font-weight: 700; color: var(--brand-blue); line-height: 22px; }
  .contact__role { font-size: 13px; color: var(--accent-orange); line-height: 16px; }
  .contact__address { margin-top: 10px; font-size: 11.5px; line-height: 14px; }
  .contact__list { list-style: none; margin-top: 10px; font-size: 11.5px; }
  .contact__list li { display: flex; align-items: center; gap: 6px; height: 17.5px; }
  .contact__list svg { width: 11px; height: 11px; flex: none; }

  .stripe-orange { position: absolute; left: 0; top: 241px; width: 100%; height: 2px; background: var(--accent-orange); }
  .stripe-blue { position: absolute; left: 0; top: 245px; width: 100%; height: 17px; background: var(--brand-blue); }

  .tagline {
    position: absolute; left: 0; top: 218px; width: 100%;
    text-align: center; color: var(--white); font-size: 13px;
  }
</style>
</head>
<body>
<main class="canvas">
  <section class="card card--front">
    <div class="brand"><span class="brand__dot"></span>Tall Pine Computing</div>
    <div class="divider"></div>
    <div class="contact">
      <p class="contact__name">Owen Carter</p>
      <p class="contact__role">CEO/Founder</p>
      <p class="contact__address">2140 Cedar Ridge Road<br>Fairview, Oregon 97024</p>
      <ul class="contact__list">
        <li>
          <svg viewBox="0 0 12 12" aria-hidden="true"><path fill="#1a8fd6" d="M2.4 0.6l1.8 0 .8 2.6-1.2 1c.6 1.3 1.6 2.3 2.9 2.9l1-1.2 2.6.8v1.8c0 .8-.6 1.3-1.4 1.2C4.6 9.3 1.6 6.2 1.2 2c-.1-.8.4-1.4 1.2-1.4z"/></svg>
          503 218 4617
        </li>
        <li>
          <svg viewBox="0 0 12 12" aria-hidden="true"><rect x="0.5" y="2" width="11" height="8" fill="#1a8fd6"/><path d="M0.5 2.5L6 6.5l5.5-4" fill="none" stroke="#f7f7f7" stroke-width="1"/></svg>
          hello@tallpinecomputing.com
        </li>
        <li>
          <svg viewBox="0 0 12 12" aria-hidden="true"><circle cx="6" cy="6" r="5.5" fill="#1a8fd6"/><path d="M6 .5v11M.5 6h11M6 .5c-2.4 2.8-2.4 8.2 0 11M6 .5c2.4 2.8 2.4 8.2 0 11" fill="none" stroke="#f7f7f7" stroke-width=".8"/></svg>
          www.tallpinecomputing.com
        </li>
      </ul>
    </div>
    <div class="stripe-orange"></div>
    <div class="stripe-blue"></div>
  </section>

  <section class="card card--back">
    <div class="brand"><span class="brand__dot"></span>Tall Pine Computing</div>
    <p class="tagline">Rooted in technology</p>
  </section>
</main>
</body>
</html>
```